Exciting & Elegant Stationary Pack

Stationary consists of
1. Letter head / Envelope
2. Business Card
3. Invoice
4. 40x40mm sticker

Attached files;

1. Logo (Other formats available on request)
2. MS word Doc - For information and description of design
3. Website image (This will be our new website so use the colours so everything ties together)
4. Sample of stationary pack we like, but feel free to be creative

Target Market(s)

Home improvement

Industry/Entity Type

Construction

Font styles to use
Other font styles liked:
• Leave up to designer - We like font used on (website attached image)

Requirements
Must have
• Please look at uploaded file of sample website and use colours
Nice to have
• Any type of business card design - eg. metal, die cut, embossed, etc...

```html
<!DOCTYPE html>
<html lang="en">
<head>
<meta charset="utf-8">
<title>Grout &amp; Level — Business Card</title>
<link href="https://fonts.googleapis.com/css2?family=Lexend:wght@300;400;600;700&display=swap" rel="stylesheet">
<style>
  :root {
    --navy: #123f65;
    --orange: #f08a38;
    --white: #ffffff;
    --backdrop: #e6e6e6;
  }
  * { margin: 0; padding: 0; box-sizing: border-box; }
  html, body { width: 1200px; height: 1037px; overflow: hidden; }
  body {
    background: var(--backdrop);
    position: relative;
    font-family: "Lexend", sans-serif;
  }
  .card {
    position: absolute;
    width: 638px;
    height: 365px;
    overflow: hidden;
  }
  .card-front { left: 159px; top: 144px; background: var(--white); }
  .card-back { left: 391px; top: 570px; }
  .front-band { position: absolute; inset: 0; }
  .tile-field { position: absolute; inset: 0; background: var(--navy); }

  .brand {
    position: absolute;
    display: flex;
    align-items: center;
    gap: 10px;
    font-weight: 700;
    font-size: 25px;
    letter-spacing: 0.5px;
    text-transform: uppercase;
    white-space: nowrap;
  }
  .brand-mark { width: 16px; height: 16px; background: var(--orange); flex: none; }
  .card-front .brand { left: 322px; top: 52px; color: var(--navy); }
  .card-back .brand { left: 348px; top: 240px; color: var(--white); }

  .holder {
    position: absolute;
    left: 56px;
    top: 262px;
  }
  .holder-name {
    color: var(--orange);
    font-weight: 600;
    font-size: 21px;
    letter-spacing: 0.4px;
  }
  .holder-role {
    color: var(--white);
    font-weight: 400;
    font-size: 15px;
    margin-top: 6px;
    letter-spacing: 0.3px;
  }
  .contact {
    position: absolute;
    right: 56px;
    top: 244px;
    text-align: right;
    color: var(--white);
    list-style: none;
    font-weight: 300;
    font-size: 14.5px;
    line-height: 25px;
    letter-spacing: 0.3px;
    text-transform: uppercase;
  }
  .contact .phone { font-size: 17px; font-weight: 400; }
  .contact .licence { font-size: 16px; font-weight: 400; margin-top: 3px; }
</style>
</head>
<body>
  <section class="card card-front">
    <svg class="front-band" width="638" height="365" viewBox="0 0 638 365" aria-hidden="true">
      <path d="M0,210 H108 C128,210 130,232 150,232 H168 C188,232 190,210 210,210 H638 V365 H0 Z" fill="var(--navy)"/>
      <path d="M0,210 H108 C128,210 130,232 150,232 H168 C188,232 190,210 210,210 H638" fill="none" stroke="var(--orange)" stroke-width="6"/>
    </svg>
    <div class="brand"><span class="brand-mark"></span>Grout &amp; Level</div>
    <div class="holder">
      <p class="holder-name">MARA ELLISON</p>
      <p class="holder-role">PROJECT MANAGER</p>
    </div>
    <ul class="contact">
      <li class="phone">P. 0400 555 123</li>
      <li>info@groutandlevel.com.au</li>
      <li>www.groutandlevel.com.au</li>
      <li class="licence">LIC NO. 204619B</li>
    </ul>
  </section>

  <section class="card card-back">
    <div class="tile-field" role="img" aria-label="Navy subway tile pattern covering the card"></div>
    <div class="brand"><span class="brand-mark"></span>Grout &amp; Level</div>
  </section>
</body>
</html>
```